Business card for Eyelash extension salon in Crestmoor Hills,California USA

We need new business card for our salon in Crestmoor Hills. The salon name is 'Lashvera' . We would like to have...Business name: Lashvera Name of person: will provide later Address 4720 N.Alder Crest Ave Crestmoor Hills , CA 90477 Phone: will provide later (Text only) Web: www.lashverastudio.example Snapgrid icon, Circlebook icon follow us for seasonal campaign and news @lashverastudiolounge Design should look elegant, high-end, clean, simple, cohesive with my brand. Please refer my brand board. Business name color will be metallic bronzy color. Im thinking grey background or white background. Thanks

Target Market(s)

25-35. Gender neutral. People who are in Entertainment business industry.
This is High-end Eyelash extension salon in Crestmoor Hills

Industry/Entity Type

Beauty Salon

Contact Information for Business Card

Business name: Lashvera
Name of person: will provide later
Address 4720 N.Alder Crest Ave Crestmoor Hills , CA 90477
Phone: will provide later (Text only)
Web: www.lashverastudio.example
Snapgrid icon, Circlebook icon
follow us for seasonal campaign and news @lashverastudiolounge

Requirements
Must have
• Beautiful, elegant, clean and simple look but very attractive and modern
Should not have
• We don't like too clutter, too busy designs.

```html
<!DOCTYPE html>
<html lang="en">
<head>
<meta charset="utf-8">
<title>Lashvera Business Card</title>
<link rel="stylesheet" href="https://fonts.googleapis.com/css2?family=Libre+Caslon+Text:wght@400;700&family=Montserrat:wght@400&display=swap">
<style>
  :root {
    --stage: #e9e7e4;
    --card: #fbfbfa;
    --bronze: #6e5340;
    --bronze-soft: #8a6c56;
    --ink: #3d2f25;
  }
  * { margin: 0; padding: 0; box-sizing: border-box; }
  html, body {
    width: 1200px; height: 780px; overflow: hidden;
    background: var(--stage);
  }
  .sheet {
    width: 1200px; height: 780px;
    display: flex; align-items: center; justify-content: center; gap: 70px;
  }
  .card {
    width: 460px; height: 460px;
    background: var(--card);
    border-radius: 34px;
    box-shadow: 0 10px 28px rgba(60, 45, 35, 0.14);
    display: flex; flex-direction: column; align-items: center; justify-content: center;
    text-align: center;
    font-family: "Libre Caslon Text", "Times New Roman", serif;
    color: var(--ink);
  }
  /* Back: contact details */
  .contact-name {
    font-weight: 700; font-size: 34px; color: var(--bronze); line-height: 1;
  }
  .contact-role {
    font-size: 14px; color: var(--bronze); margin-top: 4px; margin-bottom: 22px;
  }
  .contact-lines { font-size: 16px; line-height: 1.32; color: var(--ink); }
  .contact-web {
    font-size: 18px; letter-spacing: 1.2px; margin-top: 16px; color: var(--ink);
  }
  .social-row {
    display: flex; gap: 14px; justify-content: center; align-items: center;
    margin-top: 22px; font-size: 13px; color: var(--bronze);
  }
  .social-item { display: flex; align-items: center; gap: 5px; }
  .social-item .mark {
    width: 11px; height: 11px; border: 1.4px solid var(--bronze); border-radius: 2px;
  }
  .social-handle { font-size: 16px; margin-top: 6px; color: var(--ink); }
  /* Front: brand lockup */
  .brand-name {
    font-size: 62px; font-weight: 400; color: var(--bronze); letter-spacing: 1px; line-height: 1;
  }
  .brand-place {
    font-family: "Montserrat", Arial, sans-serif;
    font-size: 11px; letter-spacing: 4px; color: var(--bronze-soft);
    margin-top: 16px;
  }
</style>
</head>
<body>
  <main class="sheet">
    <section class="card card-back">
      <h1 class="contact-name">Marlo Keane</h1>
      <p class="contact-role">Owner</p>
      <div class="contact-lines">
        <p>P: +1 310 555 0148</p>
        <p>E: info@lashverastudio.example</p>
        <p>4720 N.Alder Crest Ave Crestmoor Hills</p>
        <p>CA 90477</p>
      </div>
      <p class="contact-web">www.lashverastudio.example</p>
      <div class="social-row">
        <span class="social-item"><span class="mark"></span>Circlebook</span>
        <span class="social-item"><span class="mark"></span>Snapgrid</span>
      </div>
      <p class="social-handle">@lashverastudiolounge</p>
    </section>
    <section class="card card-front">
      <p class="brand-name">Lashvera</p>
      <p class="brand-place">CRESTMOOR HILLS</p>
    </section>
  </main>
</body>
</html>
```